Business Card Design Project

We need a business card for a new technology services company. We develop software and implement software packages for our business customers and although we will begin with just one or two service offerings, our service offerings will expand over time. Our name comes from the an author, KL Barrow, and his "idea" was that opportunity should be based on ability and achievement, not on social status.

We would like to see a design that is standard in its size and shape, but stands apart in its dramatic color contrasts. The card should not use too many colors - the colors used in the background should highlight the brilliant blues of the logo (see attachment) to dramatic effect. The background should not be white.

If necessary, you can change the color of the words "KL Barrow", but not the word "Idea".

Card size should be U.S. standard 2 inches by 3.5 inches and provide for 1/8 inch bleed area on each side.

We need a design for both sides of the business card, one side communicating the company logo and contact information, the other side being purely graphical, incorporating the logo but no other information.

Contact Information Required:
Kate Brook
KateBrook@klbarrowvista.com
614-387-2259

Target Market(s)

Business executives

Industry/Entity Type

Software

Requirements
Must have
• It must have the full company logo on one side, and at least the graphic element of the logo on the other. Either that or the full logo on both.
Nice to have
• It would be nice to have a design that could work without needing two different textures. For example, it would be nice if the entire card could be shiny, not just parts of the card.

It would also be nice if texture is something we could add later.
Should not have
• The card should not use the color green.

```html
<!DOCTYPE html>
<html lang="en">
<head>
<meta charset="utf-8">
<title>KL Barrow Vista – Business Card</title>
<link rel="stylesheet" href="https://fonts.googleapis.com/css2?family=Arimo:wght@400;700&display=swap">
<style>
  :root {
    --page-bg: #e6e6ea;
    --card-black: #0d0f11;
    --card-charcoal: #2a2d31;
    --brand-blue: #1aa7ec;
    --brand-blue-deep: #0a78c2;
    --silver: #c8cacd;
    --text-white: #ffffff;
  }
  * { margin: 0; padding: 0; box-sizing: border-box; }
  html, body {
    width: 1200px;
    height: 987px;
    overflow: hidden;
    background: var(--page-bg);
    font-family: "Arimo", Arial, sans-serif;
  }
  .card {
    position: absolute;
    left: 250px;
    width: 700px;
    height: 400px;
    border-radius: 34px;
    overflow: hidden;
    background:
      radial-gradient(ellipse at 70% 45%, rgba(70,76,84,0.55) 0%, rgba(0,0,0,0) 60%),
      linear-gradient(160deg, var(--card-charcoal) 0%, var(--card-black) 55%, #050607 100%);
    box-shadow: 0 14px 30px rgba(0,0,0,0.18);
  }
  .card-front { top: 50px; }
  .card-back { top: 537px; }

  .swoosh { position: absolute; inset: 0; }

  .company-name {
    position: absolute;
    display: flex;
    align-items: center;
    gap: 20px;
    color: var(--text-white);
    font-weight: 700;
    letter-spacing: 0;
    white-space: nowrap;
  }
  .company-dot {
    display: inline-block;
    border-radius: 50%;
    background: var(--brand-blue);
  }
  .card-front .company-name { left: 110px; top: 78px; font-size: 38px; }
  .card-front .company-dot { width: 44px; height: 44px; }

  .card-back .company-name { left: 70px; top: 160px; font-size: 48px; }
  .card-back .company-dot { width: 80px; height: 80px; margin-left: 16px; }

  .contact-list {
    position: absolute;
    left: 110px;
    top: 168px;
    list-style: none;
    color: var(--text-white);
    font-size: 17px;
    line-height: 30px;
  }
  .contact-list li { display: flex; align-items: center; gap: 10px; }
  .contact-icon { width: 14px; height: 14px; fill: var(--brand-blue); }

  .holder-name {
    position: absolute;
    right: 48px;
    bottom: 30px;
    color: var(--text-white);
    font-weight: 700;
    font-size: 28px;
    letter-spacing: 1px;
    text-transform: uppercase;
  }
</style>
</head>
<body>

<section class="card card-front" aria-label="Business card front">
  <svg class="swoosh" viewBox="0 0 700 400" width="700" height="400" aria-hidden="true">
    <defs>
      <linearGradient id="blue-band" x1="0" y1="0" x2="1" y2="1">
        <stop offset="0" stop-color="#27b3f2"/>
        <stop offset="1" stop-color="#0a78c2"/>
      </linearGradient>
    </defs>
    <path d="M0,150 C40,300 330,350 700,262 L700,400 L0,400 Z" fill="#c8cacd"/>
    <path d="M0,170 C50,315 340,362 700,285 L700,400 L0,400 Z" fill="#0b0c0e"/>
    <path d="M0,188 C60,330 350,372 700,300 L700,400 L0,400 Z" fill="url(#blue-band)"/>
  </svg>

  <div class="company-name"><span>KL Barrow Vista</span><span class="company-dot"></span></div>

  <ul class="contact-list">
    <li>
      <svg class="contact-icon" viewBox="0 0 24 24"><path d="M6.6 10.8a15 15 0 0 0 6.6 6.6l2.2-2.2a1 1 0 0 1 1-.25 11.4 11.4 0 0 0 3.6.57 1 1 0 0 1 1 1V20a1 1 0 0 1-1 1A17 17 0 0 1 3 4a1 1 0 0 1 1-1h3.5a1 1 0 0 1 1 1c0 1.25.2 2.45.57 3.57a1 1 0 0 1-.25 1z"/></svg>
      614-387-2259
    </li>
    <li>
      <svg class="contact-icon" viewBox="0 0 24 24"><path d="M2 5h20v14H2z M2 5l10 8 10-8" fill="none" stroke="#1aa7ec" stroke-width="2"/></svg>
      KateBrook@klbarrowvista.com
    </li>
  </ul>

  <p class="holder-name">Kate Brook</p>
</section>

<section class="card card-back" aria-label="Business card back">
  <div class="company-name"><span>KL Barrow Vista</span><span class="company-dot"></span></div>
</section>

</body>
</html>
```